Business Cards - Brightpath Horizon

need to design unique business card for my mortgage business. I need to design credit card style business card for my business or any unique idea that you might have

Target Market(s)

Home Loan customers

Industry/Entity Type

Mortgage Brokerage

Contact Information for Business Card

please design credit card style or very unique style business card

Colors

Designer to choose colors to be used in the design.

Requirements
Must have
• Name
• position
• Phone number
• fax number
• email address
• website address
• social media address
• All above fields will be provided once design in finalised

```html
<!DOCTYPE html>
<html lang="en">
<head>
<meta charset="utf-8">
<title>Brightpath Horizon – Business Cards</title>
<link rel="stylesheet" href="https://fonts.googleapis.com/css2?family=Tinos:ital,wght@0,400;0,700;1,400&display=swap">
<style>
  :root {
    --backdrop: #e9e6e1;
    --card-white: #ffffff;
    --brand-blue: #0330c8;
    --brand-orange: #f7901e;
    --brand-cyan: #16a9e8;
    --pale-blue: #d6ecf8;
    --ink: #555555;
    --rule: #4a4a4a;
  }
  * { margin: 0; padding: 0; box-sizing: border-box; }
  html, body { width: 1200px; height: 960px; overflow: hidden; }
  body {
    position: relative;
    background: var(--backdrop);
    font-family: "Tinos", "Times New Roman", serif;
  }
  .card {
    position: absolute;
    width: 600px;
    height: 343px;
    overflow: hidden;
    box-shadow: 0 2px 6px rgba(0,0,0,0.25);
  }
  .card--front { left: 314px; top: 113px; background: var(--card-white); }
  .card--back { left: 312px; top: 472px; background: var(--brand-blue); }

  .decor-tree {
    position: absolute;
    left: 0; top: 0;
    width: 250px; height: 330px;
    background: radial-gradient(ellipse at 40% 40%, var(--pale-blue) 0%, rgba(214,236,248,0.6) 55%, rgba(214,236,248,0) 75%);
  }

  .brand {
    position: absolute;
    right: 40px; top: 58px;
    text-align right;
    text-align: right;
  }
  .brand__name {
    color: var(--brand-blue);
    font-size: 38px;
    font-weight: 400;
    line-height: 1.0;
  }
  .brand__tagline {
    color: var(--brand-orange);
    font-size: 14px;
    font-style: italic;
    margin-top: 6px;
  }

  .person { position: absolute; left: 38px; top: 193px; }
  .person__name { color: var(--brand-blue); font-size: 21px; font-weight: 400; letter-spacing: 0.3px; }
  .person__role { color: var(--brand-orange); font-size: 15px; margin-top: 1px; }

  .phone {
    position: absolute;
    right: 38px; top: 194px;
    color: var(--brand-blue);
    font-size: 34px;
    letter-spacing: 0.5px;
  }
  .divider {
    position: absolute;
    left: 38px; right: 38px; top: 245px;
    border-top: 1px solid var(--rule);
  }
  .contact { position: absolute; top: 256px; font-size: 14px; color: var(--ink); line-height: 19px; }
  .contact--left { left: 38px; }
  .contact--right { right: 38px; text-align: right; }
  .contact__label { color: var(--brand-blue); font-weight: 700; }

  .bands { position: absolute; left: 0; bottom: 0; }
  .website {
    position: absolute;
    right: 36px; bottom: 10px;
    color: #fff;
    font-size: 13px;
    letter-spacing: 2px;
  }

  .back-brand {
    position: absolute;
    left: 0; right: 0; top: 112px;
    text-align: center;
    color: #fff;
  }
  .back-brand__name { font-size: 44px; line-height: 1.0; font-weight: 400; }
  .back-brand__tagline { font-size: 16px; font-style: italic; margin-top: 10px; }
  .social {
    position: absolute;
    left: 241px; top: 280px;
    display: flex; gap: 4px;
  }
  .social__dot { width: 26px; height: 26px; border-radius: 50%; background: #fff; }
</style>
</head>
<body>
  <section class="card card--front">
    <div class="decor-tree" role="img" aria-label="Faint pale blue tree decoration"></div>

    <div class="brand">
      <div class="brand__name">Brightpath<br>Horizon</div>
      <div class="brand__tagline">Smart loans, Steady homes</div>
    </div>

    <div class="person">
      <div class="person__name">DANIEL REYES</div>
      <div class="person__role">CEO/FOUNDER</div>
    </div>
    <div class="phone">415 555 0182</div>
    <div class="divider"></div>

    <div class="contact contact--left">
      <div><span class="contact__label">F:</span> 415 555 0197</div>
      <div><span class="contact__label">E:</span> hello@brightpath.com</div>
    </div>
    <div class="contact contact--right">
      <div>2140 Alder Court</div>
      <div>Portland, Oregon 97205</div>
    </div>

    <svg class="bands" width="600" height="34" viewBox="0 0 600 34" aria-hidden="true">
      <polygon points="0,13 176,13 170,21 0,21" fill="var(--brand-orange)"/>
      <polygon points="180,13 356,13 350,21 174,21" fill="var(--brand-cyan)"/>
      <polygon points="372,0 600,0 600,34 350,34" fill="var(--brand-blue)"/>
      <rect x="0" y="24" width="372" height="10" fill="var(--brand-blue)" opacity="0.9"/>
    </svg>
    <div class="website">www.brightpath.com</div>
  </section>

  <section class="card card--back">
    <div class="back-brand">
      <div class="back-brand__name">Brightpath<br>Horizon</div>
      <div class="back-brand__tagline">Smart loans, Steady homes</div>
    </div>
    <div class="social" aria-label="Social media links">
      <span class="social__dot"></span>
      <span class="social__dot"></span>
      <span class="social__dot"></span>
      <span class="social__dot"></span>
    </div>
  </section>
</body>
</html>
```